Webdesign für Branchenverzeichnis
Zielgruppe
Wir-bauen-Brücken – das Branchenverzeichnis der Selbstverantwortlichen.
Der Anbieter präsentiert sich mit seinem Namen und der URL - ähnlich wie bei 'blaue Tafeln' oder Jobkranich.
Aufgabenstellung
Das Branchenverzeichnis sollte neutral und gleichzeitig hochwertig sein. Die Hauptfarben sind Gold, Schwarz und Weiß. Logo und Corporate Design wurden bereits entwickelt

```html
<!DOCTYPE html>
<html lang="de">
<head>
<meta charset="utf-8">
<title>Wir-bauen-Brücken – Suchen</title>
<link rel="stylesheet" href="https://fonts.googleapis.com/css2?family=Quicksand:wght@400;500;600;700&family=Mulish:wght@400;600;700&display=swap">
<style>
:root{
  --gold:#d4af5f;
  --dark:#3a3a3a;
  --footer:#333333;
  --ink:#2b2b2b;
  --paper:#fafafa;
  --line:#e6dcc4;
  --white:#ffffff;
  --pin-icon:#6cc3d2;
}
*{box-sizing:border-box;margin:0;padding:0}
html,body{width:1200px;height:980px;overflow:hidden;background:var(--paper);font-family:'Quicksand',sans-serif;color:var(--ink)}
.page{position:relative;width:1200px;height:980px}

.site-header{position:absolute;left:0;top:0;width:1200px;height:62px;background:var(--dark);z-index:2}
.brand{position:absolute;left:148px;top:12px;display:flex;align-items:center;gap:5px}
.brand-dot{width:9px;height:9px;border-radius:50%;background:var(--gold)}
.brand-name{font-family:'Quicksand',sans-serif;font-weight:600;font-size:10px;color:var(--gold);line-height:38px}
.main-nav a{position:absolute;top:25px;font-family:'Mulish',sans-serif;font-weight:600;font-size:8.8px;letter-spacing:1.3px;color:var(--white);text-decoration:none}
.main-nav a.active{color:var(--gold)}
.header-icons{position:absolute;left:822px;top:24px;display:flex;gap:7px;align-items:center}
.social-circle{width:13px;height:13px;border-radius:50%;border:2px solid var(--white)}
.social-square{width:13px;height:13px;border-radius:2px;background:var(--white)}
.btn-join{position:absolute;left:918px;top:17px;width:126px;height:28px;background:var(--gold);color:var(--white);font-family:'Mulish',sans-serif;font-size:8px;letter-spacing:1px;display:flex;align-items:center;justify-content:center}

.results{position:absolute;left:0;top:62px;width:600px;height:646px;background:var(--paper)}
.results-title{position:absolute;left:18px;top:36px;font-size:16px;font-weight:500;letter-spacing:.8px;color:var(--ink)}
.results-title span{color:var(--gold)}
.filter-bar{position:absolute;left:18px;top:76px;width:570px;height:42px;border-top:1px solid var(--line);border-bottom:1px solid var(--line)}
.field{position:absolute;top:8px;width:128px;height:26px;border:1px solid #e2d9c4;background:var(--white);font-size:5.5px;color:#8a8a8a;padding-left:9px;line-height:24px}
.field svg{position:absolute;right:8px;top:7px}

.company-card{position:absolute;height:94px;width:540px;background:var(--gold);box-shadow:0 3px 10px rgba(0,0,0,.12)}
.company-photo{position:absolute;left:0;top:0;width:130px;height:94px;background:linear-gradient(135deg,#c9ccd0 0%,#8c8a86 45%,#4b4a49 100%)}
.company-name{position:absolute;left:148px;top:7px;font-size:14px;font-weight:600;letter-spacing:.7px;color:var(--white)}
.company-meta{position:absolute;left:148px;top:29px;display:flex;gap:30px;font-size:7.8px;color:var(--white);font-weight:500}
.company-meta span{display:flex;align-items:center;gap:4px}
.company-desc{position:absolute;left:148px;top:53px;width:232px;font-size:8.2px;line-height:12px;color:var(--white)}
.btn-details{position:absolute;left:391px;top:32px;width:126px;height:38px;border:1px solid var(--ink);font-family:'Mulish',sans-serif;font-size:8px;letter-spacing:1px;display:flex;align-items:center;justify-content:center;color:var(--ink)}

.pagination{position:absolute;left:191px;top:596px;display:flex;gap:7px}
.pagination span{width:31px;height:31px;border:1px solid var(--gold);display:flex;align-items:center;justify-content:center;font-size:12px;color:#555}
.pagination span.current{color:var(--gold);font-weight:700}

.map-area{position:absolute;left:600px;top:62px;width:600px;height:646px;overflow:hidden}
.map-base{position:absolute;inset:0;background:
  radial-gradient(ellipse 60% 35% at 50% 105%,#a9d4df 0%,#a9d4df 60%,rgba(169,212,223,0) 100%),
  radial-gradient(ellipse 30% 25% at 88% 8%,#b3d8e0 0%,rgba(179,216,224,0) 100%),
  linear-gradient(170deg,#ece8df 0%,#e3e8da 30%,#f1e3e2 50%,#ebe4dc 65%,#b7d9e1 82%,#a6d1dc 100%)}
.map-pin{position:absolute;width:32px;height:42px}

.site-footer{position:absolute;left:0;top:708px;width:1200px;height:272px;background:var(--footer);color:var(--white)}
.footer-brand{position:absolute;left:244px;top:90px;display:flex;align-items:center;gap:5px}
.footer-brand .brand-dot{background:var(--white)}
.footer-brand .brand-name{color:var(--white);font-size:9px;line-height:14px}
.footer-about{position:absolute;left:360px;top:78px;width:184px}
.footer-about h3{font-size:11.5px;font-weight:700;margin-bottom:10px;letter-spacing:.3px}
.footer-about p{font-size:9.6px;line-height:15.6px;font-weight:400;color:#e8e8e8}
.footer-about a{display:block;margin-top:4px;font-size:10px;color:var(--gold)}
.footer-col{position:absolute;top:78px}
.footer-col h4{font-size:11.5px;font-weight:700;letter-spacing:.8px;margin-bottom:14px}
.footer-col a{display:block;font-size:9.6px;color:#e8e8e8;text-decoration:none;height:25px}
.copyright{position:absolute;left:0;top:246px;width:1200px;text-align:center;font-size:8px;font-weight:600}
</style>
</head>
<body>
<div class="page">
  <header class="site-header">
    <div class="brand"><span class="brand-dot"></span><span class="brand-name">Wir-bauen-Brücken</span></div>
    <nav class="main-nav">
      <a href="#" style="left:287px">HOME</a>
      <a href="#" class="active" style="left:362px">SUCHEN</a>
      <a href="#" style="left:450px">ÜBER UNS</a>
      <a href="#" style="left:544px">MITGLIEDSCHAFT</a>
      <a href="#" style="left:675px">KONTAKT</a>
    </nav>
    <div class="header-icons">
      <span class="social-circle"></span>
      <span class="social-square"></span>
      <svg width="14" height="14" viewBox="0 0 14 14"><circle cx="7" cy="4" r="3.2" fill="#fff"/><path d="M1 14c0-4 3-6 6-6s6 2 6 6z" fill="#fff"/></svg>
    </div>
    <div class="btn-join">MITGLIED WERDEN</div>
  </header>

  <main class="results">
    <h1 class="results-title">Wir zeigen Unternehmen für <span>IT &amp; Marketing</span></h1>
    <div class="filter-bar">
      <div class="field" style="left:0">Unternehmen, Name
        <svg width="11" height="10" viewBox="0 0 11 10"><path d="M5.5 0L0 5h1.5v5h3V7h2v3h3V5H11z" fill="#d4af5f"/></svg></div>
      <div class="field" style="left:133px">Stadt, PLZ oder Land
        <svg width="11" height="11" viewBox="0 0 11 11"><circle cx="5.5" cy="5.5" r="4" fill="none" stroke="#d4af5f" stroke-width="1.2"/><circle cx="5.5" cy="5.5" r="1.8" fill="#d4af5f"/></svg></div>
      <div class="field" style="left:266px">Sortieren nach
        <svg width="10" height="8" viewBox="0 0 10 8"><path d="M1 2l4 4 4-4" fill="none" stroke="#d4af5f" stroke-width="1.3"/></svg></div>
      <div class="field" style="left:441px">IT &amp; Marketing
        <svg width="10" height="8" viewBox="0 0 10 8"><path d="M1 2l4 4 4-4" fill="none" stroke="#d4af5f" stroke-width="1.3"/></svg></div>
    </div>

    <article class="company-card" style="left:31px;top:142px">
      <div class="company-photo" role="img" aria-label="Foto: Team bei einer Besprechung im Büro"></div>
      <h2 class="company-name">Firmenname</h2>
      <div class="company-meta"><span><svg width="7" height="7" viewBox="0 0 7 7"><rect x=".5" y="1" width="6" height="5.5" fill="none" stroke="#fff"/><rect x="2" y="3" width="2" height="2" fill="#fff"/></svg>IT &amp; Marketing</span><span><svg width="6" height="8" viewBox="0 0 6 8"><path d="M3 0a3 3 0 0 1 3 3c0 2-3 5-3 5S0 5 0 3a3 3 0 0 1 3-3z" fill="#fff"/></svg>München</span></div>
      <p class="company-desc">Lorem ipsum dolor sit amet, consectetur adipisicing elit, sed do eiusmod tempor incididunt ut labore et dolore.</p>
      <div class="btn-details">DETAILS</div>
    </article>
    <article class="company-card" style="left:31px;top:251px">
      <div class="company-photo" role="img" aria-label="Foto: Team bei einer Besprechung im Büro"></div>
      <h2 class="company-name">Firmenname</h2>
      <div class="company-meta"><span><svg width="7" height="7" viewBox="0 0 7 7"><rect x=".5" y="1" width="6" height="5.5" fill="none" stroke="#fff"/><rect x="2" y="3" width="2" height="2" fill="#fff"/></svg>IT &amp; Marketing</span><span><svg width="6" height="8" viewBox="0 0 6 8"><path d="M3 0a3 3 0 0 1 3 3c0 2-3 5-3 5S0 5 0 3a3 3 0 0 1 3-3z" fill="#fff"/></svg>München</span></div>
      <p class="company-desc">Lorem ipsum dolor sit amet, consectetur adipisicing elit, sed do eiusmod tempor incididunt ut labore et dolore.</p>
      <div class="btn-details">DETAILS</div>
    </article>
    <article class="company-card" style="left:30px;top:361px">
      <div class="company-photo" role="img" aria-label="Foto: Team bei einer Besprechung im Büro"></div>
      <h2 class="company-name">Firmenname</h2>
      <div class="company-meta"><span><svg width="7" height="7" viewBox="0 0 7 7"><rect x=".5" y="1" width="6" height="5.5" fill="none" stroke="#fff"/><rect x="2" y="3" width="2" height="2" fill="#fff"/></svg>IT &amp; Marketing</span><span><svg width="6" height="8" viewBox="0 0 6 8"><path d="M3 0a3 3 0 0 1 3 3c0 2-3 5-3 5S0 5 0 3a3 3 0 0 1 3-3z" fill="#fff"/></svg>München</span></div>
      <p class="company-desc">Lorem ipsum dolor sit amet, consectetur adipisicing elit, sed do eiusmod tempor incididunt ut labore et dolore.</p>
      <div class="btn-details">DETAILS</div>
    </article>
    <article class="company-card" style="left:30px;top:470px">
      <div class="company-photo" role="img" aria-label="Foto: Team bei einer Besprechung im Büro"></div>
      <h2 class="company-name">Firmenname</h2>
      <div class="company-meta"><span><svg width="7" height="7" viewBox="0 0 7 7"><rect x=".5" y="1" width="6" height="5.5" fill="none" stroke="#fff"/><rect x="2" y="3" width="2" height="2" fill="#fff"/></svg>IT &amp; Marketing</span><span><svg width="6" height="8" viewBox="0 0 6 8"><path d="M3 0a3 3 0 0 1 3 3c0 2-3 5-3 5S0 5 0 3a3 3 0 0 1 3-3z" fill="#fff"/></svg>München</span></div>
      <p class="company-desc">Lorem ipsum dolor sit amet, consectetur adipisicing elit, sed do eiusmod tempor incididunt ut labore et dolore.</p>
      <div class="btn-details">DETAILS</div>
    </article>

    <nav class="pagination">
      <span class="current">1</span><span>2</span><span>3</span><span>4</span><span>5</span>
    </nav>
  </main>

  <section class="map-area">
    <div class="map-base" role="img" aria-label="Stadtkarte mit Straßen, Küste und Wasserflächen"></div>
    <svg class="map-pin" style="left:150px;top:277px" viewBox="0 0 32 42" aria-label="Standort Unternehmen">
      <path d="M16 1C8 1 1.5 7.3 1.5 15.2 1.5 26 16 41 16 41s14.5-15 14.5-25.8C30.5 7.3 24 1 16 1z" fill="#fff" stroke="#e3e3e3"/>
      <circle cx="16" cy="15" r="8" fill="none" stroke="var(--pin-icon)" stroke-width="1.4"/>
      <path d="M13 11v3a3 3 0 0 0 6 0v-3M16 17v3" fill="none" stroke="var(--pin-icon)" stroke-width="1.2"/>
    </svg>
    <svg class="map-pin" style="left:260px;top:362px" viewBox="0 0 32 42" aria-label="Standort Unternehmen">
      <path d="M16 1C8 1 1.5 7.3 1.5 15.2 1.5 26 16 41 16 41s14.5-15 14.5-25.8C30.5 7.3 24 1 16 1z" fill="#fff" stroke="#e3e3e3"/>
      <circle cx="16" cy="15" r="8" fill="none" stroke="var(--pin-icon)" stroke-width="1.4"/>
      <path d="M12.5 13h7v6h-7zM14 13v-1.5a2 2 0 0 1 4 0V13" fill="none" stroke="var(--pin-icon)" stroke-width="1.2"/>
    </svg>
    <svg class="map-pin" style="left:566px;top:371px" viewBox="0 0 32 42" aria-label="Standort Unternehmen">
      <path d="M16 1C8 1 1.5 7.3 1.5 15.2 1.5 26 16 41 16 41s14.5-15 14.5-25.8C30.5 7.3 24 1 16 1z" fill="#fff" stroke="#e3e3e3"/>
      <circle cx="16" cy="15" r="8" fill="none" stroke="var(--pin-icon)" stroke-width="1.4"/>
      <path d="M12 15l4-4 4 4v4h-8z" fill="none" stroke="var(--pin-icon)" stroke-width="1.2"/>
    </svg>
  </section>

  <footer class="site-footer">
    <div class="footer-brand"><span class="brand-dot"></span><span class="brand-name">Wir-bauen-Brücken</span></div>
    <div class="footer-about">
      <h3>Wir bauen Brücken</h3>
      <p>Duis sed odio sit amet nibh vulputate cursus a sit amet mauris. Morbi accumsan ipsum velit. Nam nec tellus a</p>
      <a href="#">Über uns</a>
    </div>
    <div class="footer-col" style="left:647px">
      <h4>WEBSITE</h4>
      <a href="#">Wir bauen Brücken</a>
      <a href="#">Unternehmen suchen</a>
      <a href="#">Mitgliedschaft</a>
      <a href="#">Kontakt</a>
    </div>
    <div class="footer-col" style="left:839px">
      <h4>RECHTLICHES</h4>
      <a href="#">Impressum</a>
      <a href="#">Datenschutz</a>
      <a href="#">AGB</a>
      <a href="#">Sicherheitsbestimmungen</a>
    </div>
    <div class="copyright">© 2020 Wir Bauen Brücken</div>
  </footer>
</div>
</body>
</html>
```